Sleek wordpress site for Bramblecrest finishing works

We are a commercial job shop that serves B2B, govt & LEO and retail clients.We need a wordpress site with 6 individual pages: homepage, coating, laser engraving, laser cutting, part marking, and contact us. I have attached an outline of the desired flow and sub headings for each page. I would like to incorporate the colors of the logo through out the site to be clean and sleek enough to appeal to B2B commercial clients yet be inviting enough for retail clients.

I would like to have easy picture functionality so photographs on each page can be updated easily.

Target Market(s)

B2B industrial & Govt and Military part marking, laser engraving and coating: machine shops, aerospace companies, tool manufactures. Retail: personalized gifts, Job Shop

Coding

Coded - Design and coding required

Font styles to use
Sans Serif
Other font styles liked:
• Open to suggestion

Colors
0255a3
3176b5
eaf1f7
cfdeed
ffffff

Requirements
Must have
• Clean easy to navigate flow, separate pages as indicated on attached outline, high class feel. Great picture functionality, professional and inviting feel,
• **update: needs to be optimized for mobile, should have a gallery function. Gallery can be an additional page or embedded
Nice to have
• Social media connectivity links,
Should not have
• crappy plugins that make back-end management difficult, no blog

```html
<!DOCTYPE html>
<html lang="en">
<head>
<meta charset="utf-8">
<title>Bramblecrest Finishing Works</title>
<link href="https://fonts.googleapis.com/css2?family=Raleway:wght@400;500;600;700&display=swap" rel="stylesheet">
<style>
:root{
  --brand:#0255a3;
  --brand-mid:#3176b5;
  --brand-pale:#eaf1f7;
  --brand-soft:#cfdeed;
  --white:#ffffff;
  --ink:#222222;
  --text:#555555;
  --dark:#0b0b0b;
}
*{margin:0;padding:0;box-sizing:border-box}
html,body{width:1200px;height:3186px;overflow:hidden}
body{font-family:'Raleway',Arial,sans-serif;color:var(--ink);background:var(--white);position:relative}
.abs{position:absolute}

/* header */
.site-header{position:absolute;left:0;top:0;width:1200px;height:176px;background:var(--white)}
.brand{position:absolute;left:88px;top:62px;display:flex;align-items:center;gap:14px}
.brand-dot{width:34px;height:34px;border-radius:50%;background:var(--brand)}
.brand-name{font-size:22px;font-weight:700;color:var(--brand);text-transform:uppercase;line-height:1.15;width:230px}
.top-contact{position:absolute;right:88px;top:38px;font-size:14px;color:#333;display:flex;gap:22px;align-items:center}
.top-contact span{display:flex;align-items:center;gap:8px}
.main-nav{position:absolute;right:92px;top:102px;display:flex;gap:28px;font-size:16px;font-weight:500;color:#222}
.main-nav a{color:inherit;text-decoration:none;padding-bottom:12px}
.main-nav a.active{color:var(--brand);border-bottom:3px solid var(--brand)}

/* hero */
.hero{position:absolute;left:0;top:176px;width:1200px;height:644px;background:radial-gradient(ellipse at 50% 60%,#6b4a2c 0%,#2c2420 45%,#121416 100%);text-align:center;color:var(--white)}
.hero-eyebrow{position:absolute;top:196px;width:100%;font-size:25px;font-weight:500;letter-spacing:1px}
.hero-title{position:absolute;top:240px;width:100%;font-size:37px;font-weight:700;text-transform:uppercase}
.hero-text{position:absolute;top:310px;left:330px;width:540px;font-size:15px;line-height:27px;font-weight:500}
.btn{display:inline-flex;align-items:center;justify-content:center;border-radius:30px;font-weight:700;text-transform:uppercase;font-size:16px}
.btn-light{position:absolute;left:524px;top:390px;width:153px;height:55px;background:var(--white);color:var(--brand)}
.dots{position:absolute;display:flex;gap:10px;align-items:center}
.dot{width:11px;height:11px;border-radius:50%;background:var(--white)}
.dot.ring{width:15px;height:15px;border:2px solid var(--white);background:transparent;position:relative}
.dot.ring::after{content:"";position:absolute;left:2px;top:2px;width:7px;height:7px;border-radius:50%;background:var(--white)}

/* about */
.about-frame{left:85px;top:896px;width:268px;height:357px}
.about-photo{left:115px;top:922px;width:446px;height:306px;background:linear-gradient(135deg,#1b1d24 0%,#b32024 45%,#d9dfe6 70%,#2a9ed6 100%)}
.section-title{font-size:35px;font-weight:700;text-transform:uppercase}
.about-title{left:637px;top:928px;color:var(--brand)}
.about-text{left:641px;top:990px;width:480px;font-size:16px;line-height:27px;color:var(--text)}
.btn-brand{background:var(--brand);color:var(--white)}
.about-btn{left:641px;top:1151px;width:172px;height:55px}

/* services */
.services-bg{left:0;top:1321px;width:1200px;height:340px;background:linear-gradient(180deg,#151515 0%,#2a2826 55%,#0d0d0d 100%)}
.services-title{left:0;top:1393px;width:1200px;text-align:center;color:var(--white)}
.services-text{left:210px;top:1457px;width:780px;text-align:center;color:var(--white);font-size:16px;line-height:28px;font-weight:500}
.service-card{top:1576px;width:324px;height:253px;background:var(--dark);color:var(--white);text-align:center;padding-top:26px}
.service-card.featured{background:var(--brand)}
.service-card h3{font-size:20px;font-weight:600;margin-top:14px}
.service-card.featured h3{font-size:23px;margin-top:28px}
.service-card p{font-size:14px;font-weight:600;line-height:24px;margin:12px auto 0;width:270px}
.arrow-btn{left:571px;top:1801px;width:52px;height:52px;border-radius:50%;background:var(--dark)}

/* coating */
.coating-photo{left:0;top:1954px;width:720px;height:510px;background:radial-gradient(ellipse at 55% 60%,#f6b25a 0%,#c0581a 30%,#4a2a1c 60%,#1a1412 100%)}
.coating-title{left:622px;top:2072px;color:var(--brand)}
.coating-text{left:626px;top:2130px;width:462px;font-size:16px;line-height:27px;color:var(--text)}
.coating-btn{left:627px;top:2311px;width:153px;height:49px;font-size:15px}

/* contact */
.contact-panel{left:0;top:2464px;width:601px;height:429px;background:var(--brand);color:var(--white)}
.contact-panel h2{position:absolute;left:153px;top:80px}
.contact-item{position:absolute;left:160px;display:flex;gap:16px;font-size:18px;font-weight:700;line-height:28px}
.contact-item svg{flex:none;margin-top:4px}
.map{left:601px;top:2464px;width:599px;height:429px;background:linear-gradient(160deg,#d9d4c6 0%,#c9cdb5 40%,#a9c4de 70%,#d6d1c4 100%)}
.map-label{left:754px;top:2538px;width:319px;height:102px;background:rgba(2,85,163,.88);color:var(--white);display:flex;gap:16px;padding:22px 24px;font-size:17px;font-weight:600;line-height:27px}

/* footer */
.site-footer{left:0;top:2893px;width:1200px;height:293px;background:var(--dark);color:var(--white)}
.footer-col{position:absolute;top:48px}
.footer-col h4{font-size:18px;font-weight:700;margin-bottom:20px}
.footer-col p,.footer-col li{font-size:14px;line-height:24px;list-style:none}
.socials{display:flex;gap:13px;margin-top:22px}
.socials span{width:33px;height:33px;border-radius:50%;background:var(--brand-mid)}
.email-field{width:262px;height:37px;background:var(--white);color:#666;font-size:14px;padding:10px 14px}
.subscribe{width:163px;height:36px;margin-top:12px;background:var(--brand);color:var(--white);font-size:14px;font-weight:700;display:flex;align-items:center;justify-content:center;text-transform:uppercase}
.footer-rule{position:absolute;left:89px;top:234px;width:1022px;height:1px;background:#2b2b2b}
.copyright{position:absolute;top:254px;width:100%;text-align:center;font-size:14px}
</style>
</head>
<body>

<header class="site-header">
  <div class="brand"><span class="brand-dot"></span><span class="brand-name">Bramblecrest Finishing Works</span></div>
  <div class="top-contact">
    <span><svg width="13" height="13" viewBox="0 0 24 24"><path fill="#0255a3" d="M6.6 10.8a15 15 0 0 0 6.6 6.6l2.2-2.2a1 1 0 0 1 1-.25 11.4 11.4 0 0 0 3.6.57 1 1 0 0 1 1 1V20a1 1 0 0 1-1 1A17 17 0 0 1 3 4a1 1 0 0 1 1-1h3.5a1 1 0 0 1 1 1c0 1.25.2 2.45.57 3.57a1 1 0 0 1-.25 1z"/></svg>480.555.0186</span>
    <span>|</span>
    <span><svg width="14" height="11" viewBox="0 0 24 18"><path fill="#0255a3" d="M0 0h24v18H0z"/><path fill="none" stroke="#fff" stroke-width="2" d="M1 1l11 9 11-9"/></svg>hello@bramblecrestworks.example</span>
  </div>
  <nav class="main-nav">
    <a class="active">Home</a><a>Coating</a><a>Laser Engraving</a><a>Laser Cutting</a><a>Part Marking</a><a>Contact Us</a>
  </nav>
</header>

<section class="hero" role="img" aria-label="Industrial laser cutter throwing sparks across a metal sheet">
  <div class="hero-eyebrow">WELCOME TO</div>
  <h1 class="hero-title">Bramblecrest Finishing Works</h1>
  <p class="hero-text">Sed ut perspiciatis unde omnis iste natus error sit voluptatem accusantium doloremque laudantium, totam rem aperiam</p>
  <span class="btn btn-light">Read More</span>
  <div class="dots" style="left:570px;top:545px"><span class="dot ring"></span><span class="dot"></span><span class="dot"></span></div>
</section>

<section class="about">
  <svg class="abs about-frame" viewBox="0 0 268 357"><polygon points="0,0 268,0 116,357 0,357" fill="#0255a3"/></svg>
  <div class="abs about-photo" role="img" aria-label="Laser head engraving lettering onto a metal plate"></div>
  <h2 class="abs section-title about-title">About Us</h2>
  <p class="abs about-text">You are looking for an experienced lawyer in real estate law? You need competent support in employment law or inheritance law? Do you appreciate the advantages of personal support by the law firm owners? Welcome to Hartwell &amp; Dunmore Partners in Hamburg!</p>
  <span class="abs btn btn-brand about-btn">Read More</span>
</section>

<section class="services">
  <div class="abs services-bg" role="img" aria-label="Dark workshop background"></div>
  <h2 class="abs section-title services-title">Services</h2>
  <p class="abs services-text">Sed ut perspiciatis unde omnis iste natus error sit voluptatem accusantium doloremque laudantium, totam rem aperiam, eaque ipsa quae ab illo inventore veritatis et quasi architecto beatae vitae dicta sunt explicabo.</p>

  <div class="abs service-card" style="left:96px">
    <svg width="84" height="76" viewBox="0 0 84 76" fill="none" stroke="#fff" stroke-width="3"><rect x="8" y="6" width="52" height="52"/><circle cx="28" cy="28" r="10"/><path d="M28 38v16M42 40l30 30"/></svg>
    <h3>Laser Engraving</h3>
    <p>Sed ut perspiciatis unde omnis iste natus error sit voluptatem accusantium doloremque laudantium</p>
  </div>
  <div class="abs service-card featured" style="left:435px">
    <svg width="90" height="90" viewBox="0 0 90 90" fill="none" stroke="#fff" stroke-width="3"><rect x="15" y="8" width="60" height="10"/><path d="M35 18h20l-5 22h-10zM45 40v16M20 78h50M30 78l-8-14M60 78l8-14M45 62v10"/></svg>
    <h3>Laser Cutting</h3>
  </div>
  <div class="abs service-card" style="left:775px">
    <svg width="92" height="76" viewBox="0 0 92 76" fill="none" stroke="#fff" stroke-width="3"><circle cx="50" cy="38" r="24"/><circle cx="50" cy="38" r="10"/><path d="M4 38h36M20 26l10 12-10 12M74 38h14"/></svg>
    <h3>Part Marking</h3>
    <p>Sed ut perspiciatis unde omnis iste natus error sit voluptatem accusantium doloremque laudantium</p>
  </div>
  <svg class="abs arrow-btn" viewBox="0 0 52 52"><circle cx="26" cy="26" r="26" fill="#0b0b0b"/><path d="M14 26h22M28 18l8 8-8 8" fill="none" stroke="#fff" stroke-width="3"/></svg>
  <div class="dots" style="left:573px;top:1884px"><span class="dot" style="background:#0255a3;width:14px;height:14px"></span><span class="dot" style="background:#777"></span><span class="dot" style="background:#777"></span></div>
</section>

<section class="coating">
  <div class="abs coating-photo" role="img" aria-label="Laser cutting nozzle showering orange sparks"></div>
  <svg class="abs" style="left:476px;top:1954px" width="724" height="510" viewBox="0 0 724 510"><polygon points="226,0 724,0 724,50 196,50" fill="#eaeaea"/><polygon points="200,50 724,50 724,464 0,464" fill="#fff"/></svg>
  <h2 class="abs section-title coating-title">Coating</h2>
  <p class="abs coating-text">Ceravex is a spray on ceramic based finish that can be applied to metals,plastics, polymers and wood. The unique formulation used for Ceravex ceramiccoating enhances a number of physical performance properties includingabrasion/wear resistance, corrosion resistance, chemical resistance, impact strength, and hardness.</p>
  <span class="abs btn btn-brand coating-btn">Read More</span>
</section>

<section class="contact">
  <div class="abs contact-panel">
    <h2 class="section-title">Contact Us</h2>
    <div class="contact-item" style="top:150px"><svg width="14" height="20" viewBox="0 0 14 20"><path fill="#fff" d="M7 0a7 7 0 0 1 7 7c0 5-7 13-7 13S0 12 0 7a7 7 0 0 1 7-7zm0 4a3 3 0 1 0 0 6 3 3 0 0 0 0-6z"/></svg><span>418 W Quarry Lane #7,<br>Tempe, AZ 85281</span></div>
    <div class="contact-item" style="top:230px"><svg width="16" height="16" viewBox="0 0 24 24"><path fill="#fff" d="M6.6 10.8a15 15 0 0 0 6.6 6.6l2.2-2.2a1 1 0 0 1 1-.25 11.4 11.4 0 0 0 3.6.57 1 1 0 0 1 1 1V20a1 1 0 0 1-1 1A17 17 0 0 1 3 4a1 1 0 0 1 1-1h3.5a1 1 0 0 1 1 1c0 1.25.2 2.45.57 3.57a1 1 0 0 1-.25 1z"/></svg><span>480.555.0186</span></div>
    <div class="contact-item" style="top:288px"><svg width="17" height="13" viewBox="0 0 24 18"><path fill="#fff" d="M0 0h24v18H0z"/><path fill="none" stroke="#0255a3" stroke-width="2" d="M1 1l11 9 11-9"/></svg><span>hello@bramblecrestworks.example</span></div>
  </div>
  <div class="abs map" role="img" aria-label="Street map showing the workshop location"></div>
  <div class="abs map-label"><svg width="18" height="26" viewBox="0 0 14 20" style="flex:none"><path fill="#fff" d="M7 0a7 7 0 0 1 7 7c0 5-7 13-7 13S0 12 0 7a7 7 0 0 1 7-7zm0 4a3 3 0 1 0 0 6 3 3 0 0 0 0-6z"/></svg><span>418 W Quarry Lane #7,<br>Tempe, AZ 85281</span></div>
</section>

<footer class="abs site-footer">
  <div class="footer-col" style="left:89px;width:260px">
    <h4>About Us</h4>
    <p>But I must explain to you how all this mistaken idea of denouncing pleasure and praising pain</p>
    <div class="socials"><span></span><span></span><span></span></div>
  </div>
  <div class="footer-col" style="left:489px">
    <h4>Links</h4>
    <ul><li>Home</li><li>Coating</li><li>Laser Engraving</li><li>Laser Cutting</li><li>Part Marking</li><li>Contact Us</li></ul>
  </div>
  <div class="footer-col" style="left:848px">
    <h4>Newsletter</h4>
    <div class="email-field">Email Address</div>
    <div class="subscribe">Subscribe</div>
  </div>
  <div class="footer-rule"></div>
  <p class="copyright">© 2018 Copyrights | All Rights Reserved.</p>
</footer>

</body>
</html>
```